Selling New Product at Car Wash

Our company is introducing a new category of product never before available at automated car washes. This project involves creating signage at the entrance of the car wash to convince the car owner to purchase the product. The signage would typically be about 2 feet wide and 3 feet high in an upright metal sign holder on the pavement at the entrance of the car wash. A car owner driving into the car wash should be able to clearly see the sign, understand the benefits of the product, and be called to action (i.e. ask to have the product applied to his car).

The product, FenderGlazo, is a peel and stick clear film that protects car bumpers from scratches, nicks, scrapes and scuffs. It is applied by the car wash operator at the end of the normal wash process.

A demo website with product video is available for viewing at www.fenderglazo.biz

The signage should include the product logo (this will be supplied to the designer), some artwork (or perhaps a photo) to suggest how and where the product would appear on the car (this needs to be created by the designer), and some text describing the product benefits (suggested language to be provided by the designer). The design needs to be eye catching but not silly. Target audience will be both men and women car drivers primarily in major metropolitan areas. The final design should communicate that the product is a quick, easy, and affordable way to protect the appearance and value of the vehicle.
Updates

Project Deadline Extended
Reason: a flurry of last minute submissions require that we extend the deadline 2 more days to have time for proper review. thank you for your patience.

Target Market(s)

Car Owners who want to preserve their vehicle's appearance and value

Industry/Entity Type

It Company

Requirements
Must have
• artwork showing the product applied to a flat surface of a bumper
Nice to have
• the product ( a highly polished clear film) makes the painted surface sparkle
Should not have
• artwork should not contain bumpers with dramatic or complex curves

```html
<!DOCTYPE html>
<html lang="en">
<head>
<meta charset="utf-8">
<title>FenderGlazo – Car Wash Signage Colour Options</title>
<link rel="stylesheet" href="https://fonts.googleapis.com/css2?family=Bebas+Neue&family=Arimo:wght@400;700&family=Roboto+Condensed:wght@400;700&display=swap">
<style>
  :root {
    --page-bg: #ffffff;
    --caption: #555555;
    --black: #000000;
    --rule-grey: #5a5a5a;
    --white: #ffffff;
    --red: #b30000;
    --teal: #517a6c;
    --mint-text: #e4fff6;
    --photo-hi: #7a7a7a;
    --photo-mid: #3a3a3a;
    --photo-low: #1a1a1a;
    --photo-teal-hi: #6f9a8d;
    --photo-teal-mid: #2f4a43;
    --photo-teal-low: #0f1a17;
  }
  * { margin: 0; padding: 0; box-sizing: border-box; }
  html, body {
    width: 1200px; height: 1000px; overflow: hidden;
    background: var(--page-bg);
  }
  .board { position: relative; width: 1200px; height: 1000px; }

  .sign {
    position: absolute; top: 22px;
    width: 580px; height: 858px;
    overflow: hidden; background: var(--black);
    color: var(--white);
  }
  .sign--red { left: 12px; --brand: var(--red); --ink: var(--white);
    --hi: var(--photo-hi); --mid: var(--photo-mid); --low: var(--photo-low); }
  .sign--mono { left: 606px; --brand: var(--teal); --ink: var(--mint-text);
    --hi: var(--photo-teal-hi); --mid: var(--photo-teal-mid); --low: var(--photo-teal-low); }

  .sign__photo {
    position: absolute; left: 0; top: 180px; width: 580px; height: 480px;
    background:
      radial-gradient(ellipse 55% 10% at 40% 50%, var(--hi), transparent 75%),
      radial-gradient(ellipse 60% 14% at 55% 86%, var(--mid), transparent 75%),
      linear-gradient(180deg,
        var(--black) 0%, var(--low) 12%, var(--mid) 30%, var(--low) 38%,
        var(--mid) 46%, var(--hi) 52%, var(--mid) 58%, var(--low) 66%,
        var(--mid) 80%, var(--hi) 88%, var(--low) 94%, var(--black) 100%);
  }
  .sign__shapes { position: absolute; inset: 0; width: 580px; height: 858px; }

  .sign__logo {
    position: absolute; top: 52px; left: 0; width: 580px;
    text-align: center;
    font-family: "Bebas Neue", sans-serif;
    font-size: 56px; letter-spacing: 4px; color: var(--white);
  }
  .sign__headline {
    position: absolute; top: 222px; left: 4px; width: 580px;
    text-align: center;
    font-family: "Bebas Neue", sans-serif; font-weight: 400;
    font-size: 62px; line-height: 48px; letter-spacing: 1.5px;
    color: var(--ink);
  }
  .sign__tagline {
    position: absolute; top: 434px; left: 12px; width: 580px;
    text-align: center;
    font-family: "Arimo", sans-serif; font-size: 12px; color: var(--ink);
  }
  .sign__benefits {
    position: absolute; top: 684px; left: 32px; width: 580px;
    text-align: center;
    font-family: "Roboto Condensed", sans-serif; font-size: 15px; line-height: 15px;
    text-transform: uppercase; color: var(--ink);
  }
  .sign__benefits strong { font-weight: 700; }
  .sign__cta {
    position: absolute; top: 798px; left: 25px;
    font-family: "Bebas Neue", sans-serif; font-size: 27px;
    color: var(--white); letter-spacing: 0.5px;
  }
  .caption {
    position: absolute; top: 906px;
    font-family: "Arimo", sans-serif; font-size: 27px; color: var(--caption);
  }
  .caption--red { left: 24px; }
  .caption--mono { left: 620px; }
</style>
</head>
<body>
<main class="board">

  <section class="sign sign--red">
    <div class="sign__photo" role="img" aria-label="Close-up photo of a grey car front bumper with a clear protective film sparkling in the light"></div>
    <svg class="sign__shapes" viewBox="0 0 580 858" aria-hidden="true">
      <path d="M0 0 H580 V150 Q300 140 0 168 Z" fill="var(--brand)"/>
      <rect x="0" y="0" width="580" height="8" fill="var(--rule-grey)"/>
      <path d="M0 176 Q300 142 580 160" fill="none" stroke="var(--white)" stroke-width="5"/>
      <path d="M0 738 Q290 770 580 800 V858 H0 Z" fill="var(--rule-grey)"/>
      <path d="M0 754 Q290 784 580 816" fill="none" stroke="var(--white)" stroke-width="5"/>
      <path d="M0 762 Q290 792 580 824 V858 H0 Z" fill="var(--brand)"/>
    </svg>
    <div class="sign__logo">FenderGlazo</div>
    <h1 class="sign__headline">Protect<br>your<br>bumper</h1>
    <p class="sign__tagline">AMAZINGLY INEXPENSIVE</p>
    <p class="sign__benefits">A <strong>crystal clear</strong> removable film<br>that <strong>protects</strong> automobile bumpers<br>against tight parking, shopping cart dings,<br>garage hazards, and other minor impacts</p>
    <p class="sign__cta">Available here!</p>
  </section>

  <section class="sign sign--mono">
    <div class="sign__photo" role="img" aria-label="Close-up photo of a car front bumper with a clear protective film sparkling in the light, teal toned"></div>
    <svg class="sign__shapes" viewBox="0 0 580 858" aria-hidden="true">
      <path d="M0 0 H580 V150 Q300 140 0 168 Z" fill="var(--brand)"/>
      <path d="M0 176 Q300 142 580 160" fill="none" stroke="var(--white)" stroke-width="5"/>
      <path d="M0 754 Q290 784 580 816" fill="none" stroke="var(--white)" stroke-width="5"/>
      <path d="M0 762 Q290 792 580 824 V858 H0 Z" fill="var(--brand)"/>
    </svg>
    <div class="sign__logo">FenderGlazo</div>
    <h1 class="sign__headline">Protect<br>your<br>bumper</h1>
    <p class="sign__tagline">AMAZINGLY INEXPENSIVE</p>
    <p class="sign__benefits">A <strong>crystal clear</strong> removable film<br>that <strong>protects</strong> automobile bumpers<br>against tight parking, shopping cart dings,<br>garage hazards, and other minor impacts</p>
    <p class="sign__cta">Available here!</p>
  </section>

  <p class="caption caption--red">RED, WHITE AND GRAY</p>
  <p class="caption caption--mono">MONOCHROME</p>

</main>
</body>
</html>
```